The Ultimate Outdoor Recreation Destination

Looking for a multi purpose add design that when someone sees it, it strikes their interest to visit. This add will showcase The Hollowmere & Pickwick Lake along with some type of pic or emblems representing camping, water skiing, hunting, dirt bike and or off road adventure.

Target Market(s)

People Looking for a Getaway

Industry/Entity Type

Outdoor Recreation

Requirements
Must have
• 'Often We Already Have What we Travel to Find" Try The Hollowmere Pickwick Lake
Nice to have
• Some type of catchy phrase on the top of the add that will intrigue the reader with pics that will capture the eye. Something like, "Often We Already Have What we Travel to Find" Try The Hollowmere Pickwick Lake

```html
<!DOCTYPE html>
<html lang="en">
<head>
<meta charset="utf-8">
<title>The Hollowmere – Pickwick Lake &amp; Dam</title>
<link rel="stylesheet" href="https://fonts.googleapis.com/css2?family=Rye&family=Arvo:wght@700&display=swap">
<style>
  :root {
    --brown: #5a3a26;
    --brown-dark: #2c1d13;
    --amber: #f8a823;
    --cream: #fdf3d2;
    --frame-cream: #fbf4dc;
    --icon-ring: #e8661c;
    --white: #ffffff;
  }
  html, body {
    margin: 0;
    padding: 0;
    width: 873px;
    height: 1200px;
    overflow: hidden;
    background: var(--brown);
  }
  .poster {
    position: relative;
    width: 873px;
    height: 1200px;
    background: var(--brown);
  }
  .poster svg { display: block; }
  .title-text { font-family: "Rye", serif; fill: var(--white); }
  .subtitle-text { font-family: "Arvo", serif; font-weight: 700; fill: var(--white); }
  .headline-main { font-family: "Rye", serif; fill: var(--amber); }
  .headline-call { font-family: "Rye", serif; fill: var(--cream); }
  .activity-ring { fill: none; stroke: var(--icon-ring); stroke-width: 2.5; }
  .activity-icon { fill: none; stroke: var(--white); stroke-width: 2.2; stroke-linecap: round; stroke-linejoin: round; }
  .activity-label { font-family: "Arvo", serif; font-weight: 700; font-size: 19px; fill: var(--white); }
  .snapshot-frame { fill: var(--frame-cream); }
</style>
</head>
<body>
<main class="poster">
<svg width="873" height="1200" viewBox="0 0 873 1200" xmlns="http://www.w3.org/2000/svg">
  <defs>
    <linearGradient id="headerScene" x1="0" y1="0" x2="0" y2="1">
      <stop offset="0" stop-color="#3a2716"/>
      <stop offset="0.45" stop-color="#7a5230"/>
      <stop offset="0.8" stop-color="#9a7048"/>
      <stop offset="1" stop-color="#5a3a26"/>
    </linearGradient>
    <radialGradient id="headerGlow" cx="0.75" cy="0.2" r="0.5">
      <stop offset="0" stop-color="#e0a050" stop-opacity="0.55"/>
      <stop offset="1" stop-color="#e0a050" stop-opacity="0"/>
    </radialGradient>
    <linearGradient id="sunsetScene" x1="0" y1="0" x2="0" y2="1">
      <stop offset="0" stop-color="#6d6e96"/>
      <stop offset="0.18" stop-color="#b98aa6"/>
      <stop offset="0.38" stop-color="#f4836a"/>
      <stop offset="0.5" stop-color="#f6b463"/>
      <stop offset="0.53" stop-color="#2f2430"/>
      <stop offset="0.62" stop-color="#e56a55"/>
      <stop offset="0.8" stop-color="#a84a4c"/>
      <stop offset="1" stop-color="#3d2a38"/>
    </linearGradient>
    <linearGradient id="lodgeScene" x1="0" y1="0" x2="0" y2="1">
      <stop offset="0" stop-color="#7f95a8"/>
      <stop offset="0.4" stop-color="#6b4a2e"/>
      <stop offset="1" stop-color="#c28448"/>
    </linearGradient>
    <linearGradient id="atvScene" x1="0" y1="0" x2="0" y2="1">
      <stop offset="0" stop-color="#c3d3df"/>
      <stop offset="0.45" stop-color="#8a8f7a"/>
      <stop offset="1" stop-color="#5d6e46"/>
    </linearGradient>
    <linearGradient id="fishingScene" x1="0" y1="0" x2="1" y2="1">
      <stop offset="0" stop-color="#8a978a"/>
      <stop offset="0.55" stop-color="#6f7a64"/>
      <stop offset="1" stop-color="#d6b23a"/>
    </linearGradient>
    <linearGradient id="grillScene" x1="0" y1="0" x2="1" y2="1">
      <stop offset="0" stop-color="#4a2a1a"/>
      <stop offset="0.5" stop-color="#a5452a"/>
      <stop offset="1" stop-color="#3a3030"/>
    </linearGradient>
    <filter id="dropShadow" x="-10%" y="-10%" width="130%" height="140%">
      <feDropShadow dx="0" dy="6" stdDeviation="6" flood-color="#000" flood-opacity="0.45"/>
    </filter>
  </defs>

  <!-- header -->
  <g class="header">
    <rect role="img" aria-label="Photo of the rustic wooden lodge storefront with string lights at dusk" x="0" y="0" width="873" height="262" fill="url(#headerScene)"/>
    <rect x="0" y="0" width="873" height="262" fill="url(#headerGlow)"/>
    <text class="title-text" x="440" y="66" font-size="46" text-anchor="middle">THE</text>
    <text class="title-text" x="440" y="166" font-size="92" text-anchor="middle" textLength="600" lengthAdjust="spacingAndGlyphs">HOLLOWMERE</text>
    <text class="subtitle-text" x="440" y="220" font-size="36" text-anchor="middle" textLength="420" lengthAdjust="spacingAndGlyphs">PICKWICK LAKE &amp; DAM</text>
  </g>

  <!-- featured lake photo -->
  <g class="feature-photo">
    <rect x="17" y="253" width="839" height="360" rx="24" fill="var(--amber)"/>
    <rect role="img" aria-label="Photo of a vivid sunset over Pickwick Lake with wooded hills" x="30" y="266" width="813" height="340" rx="16" fill="url(#sunsetScene)"/>
  </g>

  <!-- snapshot row -->
  <g class="snapshots">
    <g transform="rotate(-3 108 658)" filter="url(#dropShadow)">
      <rect class="snapshot-frame" x="-5" y="558" width="226" height="200"/>
      <rect role="img" aria-label="Photo of the wooden lodge lit up in the evening" x="6" y="568" width="204" height="178" fill="url(#lodgeScene)"/>
    </g>
    <g transform="rotate(3 315 672)" filter="url(#dropShadow)">
      <rect class="snapshot-frame" x="202" y="577" width="226" height="190"/>
      <rect role="img" aria-label="Photo of a family on ATVs and off-road vehicles" x="212" y="587" width="206" height="170" fill="url(#atvScene)"/>
    </g>
    <g transform="rotate(-3 540 652)" filter="url(#dropShadow)">
      <rect class="snapshot-frame" x="427" y="557" width="226" height="190"/>
      <rect role="img" aria-label="Photo of two anglers holding largemouth bass" x="437" y="567" width="206" height="170" fill="url(#fishingScene)"/>
    </g>
    <g transform="rotate(4 760 650)" filter="url(#dropShadow)">
      <rect class="snapshot-frame" x="645" y="555" width="232" height="190"/>
      <rect role="img" aria-label="Photo of barbecue ribs on a smoker grill" x="655" y="565" width="212" height="170" fill="url(#grillScene)"/>
    </g>
  </g>

  <!-- headline -->
  <g class="headline">
    <text class="headline-main" x="436" y="876" font-size="90" text-anchor="middle" textLength="810" lengthAdjust="spacingAndGlyphs">OFTEN WE ALREADY</text>
    <text class="headline-main" x="436" y="939" font-size="56" text-anchor="middle" textLength="812" lengthAdjust="spacingAndGlyphs">HAVE WHAT WE TRAVEL TO FIND</text>
    <line x1="31" y1="962" x2="406" y2="962" stroke="var(--cream)" stroke-width="3"/>
    <line x1="464" y1="962" x2="856" y2="962" stroke="var(--cream)" stroke-width="3"/>
    <rect x="424" y="951" width="22" height="22" transform="rotate(45 435 962)" fill="var(--cream)"/>
    <text class="headline-call" x="436" y="1031" font-size="50" text-anchor="middle" textLength="818" lengthAdjust="spacingAndGlyphs">TRY THE HOLLOWMERE PICKWICK LAKE</text>
  </g>

  <!-- activities -->
  <g class="activities">
    <g class="activity camping">
      <circle class="activity-ring" cx="78" cy="1100" r="45"/>
      <path class="activity-icon" d="M52 1122 L78 1078 L104 1122 Z M72 1122 L78 1105 L84 1122 M46 1122 H110 M56 1095 V1122 M100 1095 V1122 M56 1080 a6 10 0 1 0 0.1 0 M100 1080 a6 10 0 1 0 0.1 0"/>
      <text class="activity-label" x="78" y="1176" text-anchor="middle">Camping</text>
    </g>
    <g class="activity water-skiing">
      <circle class="activity-ring" cx="253" cy="1100" r="45"/>
      <path class="activity-icon" d="M236 1080 H284 M236 1076 V1084 M238 1110 L262 1106 M226 1122 q6 -5 12 0 t12 0 t12 0 t12 0 t12 0"/>
      <text class="activity-label" x="253" y="1176" text-anchor="middle">Water Skiing</text>
    </g>
    <g class="activity hunting">
      <circle class="activity-ring" cx="439" cy="1100" r="45"/>
      <path class="activity-icon" d="M425 1100 Q412 1090 414 1072 M414 1084 L406 1080 M418 1078 L416 1068 M453 1100 Q466 1090 464 1072 M464 1084 L472 1080 M460 1078 L462 1068 M425 1100 L430 1118 L439 1128 L448 1118 L453 1100 Z"/>
      <text class="activity-label" x="439" y="1176" text-anchor="middle">Hunting</text>
    </g>
    <g class="activity dirt-bike">
      <circle class="activity-ring" cx="625" cy="1100" r="45"/>
      <path class="activity-icon" d="M596 1110 a10 10 0 1 0 20 0 a10 10 0 1 0 -20 0 M634 1110 a10 10 0 1 0 20 0 a10 10 0 1 0 -20 0 M606 1110 L620 1094 H636 L644 1110 M620 1094 L616 1086 H628 M636 1094 L632 1084"/>
      <text class="activity-label" x="625" y="1176" text-anchor="middle">Dirt Bike</text>
    </g>
    <g class="activity off-road">
      <circle class="activity-ring" cx="802" cy="1100" r="45"/>
      <path class="activity-icon" d="M776 1088 H828 V1118 H776 Z M782 1078 H822 L826 1088 H778 Z M786 1070 H818 M784 1118 V1126 H794 V1118 M810 1118 V1126 H820 V1118 M790 1100 H814 M784 1108 h6 M814 1108 h6"/>
      <text class="activity-label" x="802" y="1164" text-anchor="middle">Off Road</text>
      <text class="activity-label" x="802" y="1186" text-anchor="middle">Adventure</text>
    </g>
  </g>
</svg>
</main>
</body>
</html>
```